Brookvane Consulting Business Card Design

Business Card Design for Brookvane Consulting. Brookvane Consulting is a boutique consultancy based in Atlanta, GA., that specializes in marketing strategy, organization planning, and leadership development. We provide solutions for small businesses and startups as well as Vantage 300 companies.

http://brookvaneconsulting.com/

Target Market(s)

We provide solutions for small businesses and startups as well as Vantage 300 companies.

Industry/Entity Type

Consulting

Contact Information for Business Card

Two sided business card with priority on contact information, logo, tag line (Guidance to Plan Ahead, Grow Wider, Lead Further)

Colors

Designer to choose colors to be used in the design.

Requirements
Must have
• contact information, logo, tag line (Guidance to Plan Ahead, Grow Wider, Lead Further)
• Simple no over communication.
Nice to have
• I would like to see different placements of logo and creative use of both sides of the card
Should not have
• Do not put too much information on the card.

```html
<!DOCTYPE html>
<html lang="en">
<head>
<meta charset="utf-8">
<title>Brookvane Consulting Business Card</title>
<link href="https://fonts.googleapis.com/css2?family=Lato:wght@400;700;900&display=swap" rel="stylesheet">
<style>
  :root {
    --backdrop: #3a3431;
    --card: #0d0d0d;
    --card-edge: #1c1c1c;
    --ink: #f2f2f2;
    --ink-soft: #bdbdbd;
    --ink-muted: #8a8a8a;
    --rule: #4a4a4a;
  }
  * { margin: 0; padding: 0; box-sizing: border-box; }
  html, body {
    width: 1200px;
    height: 900px;
    overflow: hidden;
    background: var(--backdrop);
    font-family: "Lato", Arial, sans-serif;
  }
  .canvas {
    width: 1200px;
    height: 900px;
    display: flex;
    align-items: center;
    justify-content: center;
    gap: 50px;
  }
  .card {
    width: 540px;
    height: 310px;
    background: var(--card);
    border: 1px solid var(--card-edge);
    border-radius: 3px;
    box-shadow: 0 14px 30px rgba(0,0,0,0.45);
    position: relative;
    color: var(--ink);
  }

  /* Contact side */
  .card--contact {
    display: flex;
    align-items: center;
  }
  .contact-brand {
    width: 250px;
    padding-left: 38px;
  }
  .brand-name {
    font-weight: 900;
    font-size: 34px;
    line-height: 1;
    color: var(--ink);
    display: flex;
    align-items: center;
    gap: 10px;
  }
  .brand-mark {
    width: 12px;
    height: 12px;
    background: var(--ink);
    flex: none;
  }
  .brand-sub {
    font-weight: 400;
    font-size: 13px;
    letter-spacing: 3px;
    color: var(--ink-soft);
    margin-top: 8px;
    padding-left: 22px;
    text-transform: uppercase;
  }
  .contact-divider {
    width: 1px;
    height: 200px;
    background: var(--rule);
  }
  .contact-details {
    padding-left: 30px;
  }
  .person-name {
    font-weight: 700;
    font-size: 17px;
    letter-spacing: 0.5px;
    text-transform: uppercase;
  }
  .person-role {
    font-size: 13px;
    color: var(--ink-soft);
    margin-top: 2px;
  }
  .contact-list {
    list-style: none;
    margin-top: 30px;
  }
  .contact-list li {
    display: flex;
    align-items: center;
    gap: 9px;
    font-size: 13px;
    color: var(--ink);
    margin-bottom: 7px;
  }
  .contact-list svg { width: 11px; height: 11px; flex: none; }

  /* Logo side */
  .card--brand {
    display: flex;
    flex-direction: column;
    align-items: center;
    justify-content: center;
  }
  .card--brand .brand-name { font-size: 52px; gap: 14px; }
  .card--brand .brand-mark { width: 16px; height: 16px; }
  .card--brand .brand-sub {
    font-size: 18px;
    letter-spacing: 5px;
    padding-left: 30px;
    margin-top: 10px;
  }
  .tagline {
    margin-top: 42px;
    font-weight: 700;
    font-size: 12px;
    letter-spacing: 1px;
    color: var(--ink-muted);
    text-transform: uppercase;
  }
</style>
</head>
<body>
  <main class="canvas">
    <section class="card card--contact" aria-label="Card back with contact details">
      <div class="contact-brand">
        <div class="brand-name"><span class="brand-mark"></span>Brookvane</div>
        <div class="brand-sub">Consulting</div>
      </div>
      <div class="contact-divider"></div>
      <div class="contact-details">
        <p class="person-name">Daniel Hartwell</p>
        <p class="person-role">Managing Director</p>
        <ul class="contact-list">
          <li>
            <svg viewBox="0 0 12 12" aria-hidden="true"><path fill="#f2f2f2" d="M2.5 0.8l2 2-1 1.3c.6 1.4 1.9 2.8 3.4 3.4l1.3-1 2 2-1.2 1.8C5 10 1.8 6.9 0.7 2.2z"/></svg>
            444 555 0142
          </li>
          <li>
            <svg viewBox="0 0 12 12" aria-hidden="true"><rect x="0.5" y="2.5" width="11" height="7.5" fill="#f2f2f2"/><path d="M0.8 2.8L6 7l5.2-4.2" fill="none" stroke="#0d0d0d" stroke-width="1"/></svg>
            info@brookvanemail.com
          </li>
          <li>
            <svg viewBox="0 0 12 12" aria-hidden="true"><circle cx="6" cy="6" r="5.5" fill="#f2f2f2"/><path d="M0.5 6h11M6 0.5c-2.5 3-2.5 8 0 11M6 0.5c2.5 3 2.5 8 0 11" fill="none" stroke="#0d0d0d" stroke-width="0.8"/></svg>
            www.brookvaneconsulting.com
          </li>
        </ul>
      </div>
    </section>

    <section class="card card--brand" aria-label="Card front with name and tagline">
      <div class="brand-name"><span class="brand-mark"></span>Brookvane</div>
      <div class="brand-sub">Consulting</div>
      <p class="tagline">Guidance to Plan Ahead, Grow Wider, Lead Further</p>
    </section>
  </main>
</body>
</html>
```